Website for IT consulting Company

I need a website upgrade, the existing site content is ok, I would also like to add a testimonial page, the site should be something that is easy for us to update content. You use the content from www.kelvanbrook.com as an example. I will also post update logo and artwork. I also need a contact form with some type of validation or captcha.

I added Coded to the Project

Please omit Address maps

Target Market(s)

small business, service oriented companies. We provide IT Consulting, support and mangement

Industry/Entity Type

Information Technology

Coding

Number of Pages Required

1 page

Font styles to use
Serif
Sans Serif

Requirements
Must have
• Contain logo attached, and content from existing web site www.kelvanbrook.com.
• Also need to update content easily, and be movable to different platforms.
• There is a catch phrase
• "Let us worry about your technology…” “ so you don’t have to!”
• Should be included.
Nice to have
• Testimonial page, Project page where we can post new and past projects and pictures
Should not have
• none

```html
<!DOCTYPE html>
<html lang="en">
<head>
<meta charset="utf-8">
<title>Kelvanbrook – IT Solutions</title>
<link href="https://fonts.googleapis.com/css2?family=Open+Sans:wght@300;400;600&display=swap" rel="stylesheet">
<style>
:root{
  --blue:#1e8fd0;
  --blue-dark:#1572b8;
  --orange:#f08a24;
  --ink:#333;
  --muted:#777;
  --band:#f1f1f1;
  --footer:#333;
  --white:#fff;
}
*{box-sizing:border-box;margin:0;padding:0}
html,body{width:734px;height:1200px;overflow:hidden;background:var(--white);font-family:"Open Sans",Arial,sans-serif;color:var(--ink)}
.page{position:relative;width:734px;height:1200px}
.wrap{position:absolute;left:81px;width:572px}

/* header */
.site-header{position:absolute;top:0;left:0;width:734px;height:82px}
.brand{position:absolute;left:81px;top:28px;display:flex;align-items:center;gap:7px}
.brand-mark{width:18px;height:18px;background:var(--orange)}
.brand-name{font-size:21px;font-weight:600;color:#7d7d7d;line-height:1}
.header-mail{position:absolute;right:81px;top:17px;font-size:12.5px;color:#444;display:flex;align-items:center;gap:5px}
.main-nav{position:absolute;right:81px;top:52px;display:flex;gap:22px;font-size:7.5px;color:#444}
.main-nav .active{color:var(--orange)}

/* hero */
.hero{position:absolute;top:82px;left:0;width:734px;height:293px;background:radial-gradient(ellipse at 62% 55%,#3b5e86 0%,#223a5a 45%,#131f33 100%)}
.hero-title{position:absolute;left:81px;top:97px;font-size:20px;font-weight:300;color:var(--white);line-height:22px}
.hero-title span{display:block;padding-left:25px}
.slider-arrow{position:absolute;width:10px;height:16px}

/* intro */
.intro{top:400px;text-align:center}
.intro h1{font-size:20px;font-weight:300;color:var(--blue)}
.intro h2{font-size:9px;font-weight:600;letter-spacing:.3px;margin-top:5px}
.intro p{font-size:7.2px;color:var(--muted);line-height:13.5px;margin-top:8px}
.btn-more{display:inline-block;margin-top:13px;border:1px solid #ccc;padding:6px 10px;font-size:6px;color:#555}

/* services */
.services{top:576px;display:flex;justify-content:space-between}
.service{width:174px;text-align:center}
.service-icon{width:59px;height:59px;margin:0 auto;border-radius:6px;background:linear-gradient(135deg,#2aa6e6,var(--blue-dark));display:flex;align-items:center;justify-content:center}
.service h3{font-size:12px;font-weight:400;color:var(--blue);margin-top:9px;line-height:15px}
.service p{font-size:5.8px;color:#666;line-height:10.8px;margin-top:7px}

/* testimonial */
.testimonial-band{position:absolute;top:750px;left:0;width:734px;height:216px;background:var(--band)}
.testimonial-card{position:absolute;left:81px;top:40px;width:572px;height:136px;background:var(--white);text-align:center;padding-top:24px}
.testimonial-card blockquote{font-size:9px;color:#555;line-height:13.5px;padding:0 15px}
.avatar{width:40px;height:40px;border-radius:50%;background:linear-gradient(#d9d9d9,#9a9a9a);margin:8px auto 0}
.testimonial-card cite{display:block;font-style:normal;font-size:7px;color:#666;margin-top:9px}

/* support list */
.support{top:1012px}
.support h2{text-align:center;font-size:11.5px;font-weight:400;color:var(--blue)}
.support-list{list-style:none;display:grid;grid-template-columns:232px 227px 113px;row-gap:10px;margin-top:25px}
.support-list li{display:flex;align-items:center;gap:10px;font-size:8.3px;font-weight:600;color:#333;letter-spacing:.1px}
.support-list svg{width:8px;height:8px}

/* footer */
.site-footer{position:absolute;top:1126px;left:0;width:734px;height:74px;background:var(--footer)}
.footer-nav{position:absolute;left:81px;top:27px;font-size:6px;color:#ddd;word-spacing:2px}
.copyright{position:absolute;left:81px;top:45px;font-size:6px;color:#ccc}
.social{position:absolute;right:81px;top:28px;display:flex;gap:5px}
.social span{width:15px;height:15px;border-radius:50%;background:#2c7fc4}
</style>
</head>
<body>
<div class="page">

  <header class="site-header">
    <div class="brand">
      <span class="brand-mark"></span>
      <span class="brand-name">Kelvanbrook</span>
    </div>
    <div class="header-mail">
      <svg width="11" height="9" viewBox="0 0 11 9"><rect width="11" height="9" rx="1" fill="#444"/><path d="M0.5 1 5.5 5 10.5 1" stroke="#fff" fill="none"/></svg>
      info@kelvanbrook.com
    </div>
    <nav class="main-nav">
      <span class="active">Home</span><span>About</span><span>Support</span><span>clients</span><span>careers</span><span>Contact</span>
    </nav>
  </header>

  <section class="hero" role="img" aria-label="Business person holding a tablet with a glowing cloud network of connected devices">
    <h2 class="hero-title">Flexible solutions for<span>your business needs</span></h2>
    <svg class="slider-arrow" style="left:14px;top:138px" viewBox="0 0 10 16"><path d="M8 1 2 8l6 7" stroke="#fff" stroke-opacity=".7" stroke-width="2" fill="none"/></svg>
    <svg class="slider-arrow" style="right:14px;top:138px" viewBox="0 0 10 16"><path d="M2 1l6 7-6 7" stroke="#fff" stroke-opacity=".7" stroke-width="2" fill="none"/></svg>
  </section>

  <section class="wrap intro">
    <h1>IT solutions that work for your business</h1>
    <h2>A FULL SERVICE TECHNOLOGY COMPANY</h2>
    <p>Outsourcing is subcontracting a process, such as product design or manufacturing, to a third-party company.[1] The decision to outsource is often made in the interest of lowering firm costs, redirecting or conserving energy directed at the competencies of a particular business, or to make more efficient use of land, labor, capital, (information) technology and resources. Outsourcing became part of the business lexicon during the 1980s.</p>
    <span class="btn-more">Learn more</span>
  </section>

  <section class="wrap services">
    <article class="service">
      <div class="service-icon"><svg width="26" height="22" viewBox="0 0 26 22"><circle cx="9" cy="12" r="6" fill="none" stroke="#fff" stroke-width="4" stroke-dasharray="3 1.7"/><circle cx="19" cy="6" r="3.5" fill="none" stroke="#fff" stroke-width="2.5" stroke-dasharray="2 1.2"/><circle cx="20" cy="16" r="3" fill="none" stroke="#fff" stroke-width="2.5" stroke-dasharray="2 1.2"/></svg></div>
      <h3>Managed IT Solutions</h3>
      <p>Our staff will design, service, administer and maintain your IT needs. We are well versed on all major operating system, and network appliances.</p>
    </article>
    <article class="service">
      <div class="service-icon"><svg width="28" height="24" viewBox="0 0 28 24"><rect x="1" y="1" width="26" height="17" rx="2" fill="none" stroke="#fff" stroke-width="2.5"/><rect x="11" y="18" width="6" height="3" fill="#fff"/><rect x="7" y="21" width="14" height="2" fill="#fff"/></svg></div>
      <h3>Remote Diagnostic and<br>Support</h3>
      <p>Do you need a quick solution to a technical problem? With our live remote-assistance tool, a member of our support team can view your desktop and share control of your mouse and keyboard to get you on your way to a solution.</p>
    </article>
    <article class="service">
      <div class="service-icon"><svg width="26" height="22" viewBox="0 0 26 22"><rect x="10" y="1" width="6" height="5" fill="#fff"/><rect x="1" y="16" width="6" height="5" fill="#fff"/><rect x="10" y="16" width="6" height="5" fill="#fff"/><rect x="19" y="16" width="6" height="5" fill="#fff"/><path d="M13 6v10M4 16v-5h18v5" stroke="#fff" stroke-width="1.6" fill="none"/></svg></div>
      <h3>IT Infrastructure Design and<br>Installation</h3>
      <p>Do you have more than one site? Do you need remote access? We can design and implement LANS/WANS and VPN's. Make your important data available to you wherever you are.</p>
    </article>
  </section>

  <section class="testimonial-band">
    <svg class="slider-arrow" style="left:14px;top:107px" viewBox="0 0 10 16"><path d="M8 1 2 8l6 7" stroke="#bbb" stroke-width="1.5" fill="none"/></svg>
    <svg class="slider-arrow" style="right:14px;top:107px" viewBox="0 0 10 16"><path d="M2 1l6 7-6 7" stroke="#bbb" stroke-width="1.5" fill="none"/></svg>
    <div class="testimonial-card">
      <blockquote>“ Proin eleifend accumsan magna, ac consequat ante blandit id. Nunc sit amet ac est feugiat tempus. Ut felis metus, viverra eget hendrerit eu, congue fermentum diam venenatis est est, in elementum consectetur. ”</blockquote>
      <div class="avatar" role="img" aria-label="Portrait photo of the client"></div>
      <cite>- Mara Dent, City</cite>
    </div>
  </section>

  <section class="wrap support">
    <h2>IT Support Solutions</h2>
    <ul class="support-list">
      <li><svg viewBox="0 0 8 8"><circle cx="4" cy="4" r="3.6" fill="#333"/><path d="M1 3h6M1 5h6M4 .5v7" stroke="#fff" stroke-width=".6"/></svg>NETWORK ADMINISTRATION</li>
      <li><svg viewBox="0 0 8 8"><rect x=".5" y="2.5" width="7" height="4" fill="none" stroke="#333"/><rect x="2" y=".5" width="4" height="2" fill="none" stroke="#333"/></svg>NETWORK CABLING</li>
      <li><svg viewBox="0 0 8 8"><path d="M4 .3 7.2 1.5v2.3C7.2 6 5.5 7.3 4 7.8 2.5 7.3.8 6 .8 3.8V1.5z" fill="#333"/></svg>ANTIVIRUS SOLUTIONS</li>
      <li><svg viewBox="0 0 8 8"><rect x=".5" y=".8" width="7" height="5" fill="none" stroke="#333"/><rect x="2" y="6.5" width="4" height="1.2" fill="#333"/></svg>DESKTOP SUPPORT</li>
      <li><svg viewBox="0 0 8 8"><path d="M.5 3a5 5 0 0 1 7 0M1.8 4.5a3 3 0 0 1 4.4 0" stroke="#333" stroke-width="1" fill="none"/><circle cx="4" cy="6.5" r="1" fill="#333"/></svg>WIRELESS NETWORKS</li>
      <li><svg viewBox="0 0 8 8"><rect x="1.3" y="3.5" width="5.4" height="4.2" fill="#333"/><path d="M2.5 3.5V2.3a1.5 1.5 0 0 1 3 0v1.2" stroke="#333" fill="none"/></svg>NETWORK SECURITY</li>
    </ul>
  </section>

  <footer class="site-footer">
    <nav class="footer-nav">Home | About | Support | Clients | Careers | Contact</nav>
    <p class="copyright">Copyright © 2017 Company name. All rights reserved.</p>
    <div class="social"><span></span><span></span><span></span></div>
  </footer>

</div>
</body>
</html>
```